Card Design for my dog training business Brightpaw Obedience

Need a business card design for my dog training business with my new logo. Want the card to come off professional yet fun. Want it to be very eye catchy as well. I normally have these at vet clinics, pet stores, and groomers. so need it to look better than my competitors.
Target Market(s)
dog owners
Industry/Entity Type
Dog Training
Contact Information for Business Card
needs logo, my name and info
Font styles to use
Serif
Colors
0255a3
ffffff
ec1f27
000000
333333
fbfbfb
Requirements
Must have
- Brightpaw Obedience
- Felix Orland
- 415 903 2276
- info@brightpawobedience.example
- www.brightpawobedience.example

```html
<!DOCTYPE html>
<html lang="en">
<head>
<meta charset="utf-8">
<title>Brightpaw Obedience – Business Card</title>
<link rel="stylesheet" href="https://fonts.googleapis.com/css2?family=Caladea:ital,wght@0,400;1,400&family=Open+Sans:wght@400&display=swap">
<style>
  :root {
    --brand-blue: #034b8e;
    --ink-black: #0a0a0a;
    --paper: #f4f4f4;
    --text-dark: #333333;
    --text-mid: #555555;
    --white: #ffffff;
    --backdrop: #c4c4c4;
  }
  * { margin: 0; padding: 0; box-sizing: border-box; }
  html, body {
    width: 1200px;
    height: 576px;
    overflow: hidden;
    background: var(--backdrop);
  }
  .stage { position: relative; width: 1200px; height: 576px; }

  .card {
    position: absolute;
    border-radius: 13px;
    overflow: hidden;
  }

  /* Front side */
  .card-front {
    left: 82px; top: 139px;
    width: 484px; height: 293px;
    background: var(--brand-blue);
  }
  .front-brand {
    position: absolute;
    left: 0; right: 0; top: 78px;
    text-align: center;
    font-family: "Caladea", Georgia, serif;
    font-weight: 400;
    font-size: 34px;
    line-height: 40px;
    color: var(--white);
  }
  .tagline-band {
    position: absolute;
    left: 0; right: 0; top: 255px;
    height: 28px;
    background: var(--ink-black);
    display: flex; align-items: center; justify-content: center;
  }
  .tagline {
    font-family: "Caladea", Georgia, serif;
    font-style: italic;
    font-size: 11.5px;
    color: var(--white);
  }

  /* Back side */
  .card-back {
    left: 602px; top: 138px;
    width: 481px; height: 291px;
    background: var(--paper);
  }
  .back-brand {
    position: absolute;
    left: 30px; width: 180px; top: 106px;
    text-align: center;
    font-family: "Caladea", Georgia, serif;
    font-weight: 400;
    font-size: 28px;
    line-height: 33px;
    color: var(--text-dark);
  }
  .person {
    position: absolute;
    left: 259px; top: 84px;
  }
  .person-name {
    font-family: "Caladea", Georgia, serif;
    font-size: 20px;
    line-height: 24px;
    color: var(--brand-blue);
  }
  .person-role {
    font-family: "Open Sans", Arial, sans-serif;
    font-size: 11.5px;
    line-height: 16px;
    color: var(--text-mid);
    margin-top: 1px;
  }
  .contact-list {
    position: absolute;
    left: 264px; top: 144px;
    list-style: none;
  }
  .contact-item {
    display: flex; align-items: center;
    height: 19px;
    font-family: "Open Sans", Arial, sans-serif;
    font-size: 11px;
    color: var(--text-dark);
  }
  .contact-icon {
    width: 10px; height: 10px;
    margin-right: 7px;
    fill: var(--brand-blue);
    flex: none;
  }
</style>
</head>
<body>
<main class="stage">
  <section class="card card-front" aria-label="Card front">
    <div class="front-brand">Brightpaw<br>Obedience</div>
    <div class="tagline-band">
      <p class="tagline">“Training dogs across Texas one dog at a time.”</p>
    </div>
  </section>

  <section class="card card-back" aria-label="Card back">
    <div class="back-brand">Brightpaw<br>Obedience</div>

    <div class="person">
      <h1 class="person-name">Felix Orland</h1>
      <p class="person-role">Dog Trainer</p>
    </div>

    <ul class="contact-list">
      <li class="contact-item">
        <svg class="contact-icon" viewBox="0 0 10 10" aria-hidden="true">
          <path d="M1 3.2 C1 1.6 2.6 1 5 1 C7.4 1 9 1.6 9 3.2 L7 3.6 L6.6 2.6 H3.4 L3 3.6 Z"/>
          <path d="M2.4 4.4 H7.6 L8.6 8.6 H1.4 Z"/>
        </svg>
        <span>415 903 2276</span>
      </li>
      <li class="contact-item">
        <svg class="contact-icon" viewBox="0 0 10 10" aria-hidden="true">
          <path d="M0.5 2 H9.5 V8 H0.5 Z M1.3 2.6 L5 5.4 L8.7 2.6 Z" fill-rule="evenodd"/>
        </svg>
        <span>info@brightpawobedience.example</span>
      </li>
      <li class="contact-item">
        <svg class="contact-icon" viewBox="0 0 10 10" aria-hidden="true">
          <circle cx="5" cy="5" r="4.5"/>
          <path d="M0.5 5 H9.5 M5 0.5 C2.8 3 2.8 7 5 9.5 M5 0.5 C7.2 3 7.2 7 5 9.5" stroke="#f4f4f4" stroke-width="0.7" fill="none"/>
        </svg>
        <span>www.brightpawobedience.example</span>
      </li>
    </ul>
  </section>
</main>
</body>
</html>
```